Maple Drift Flakes

We are a start up cereal company that has a logo/box design but are looking for something modern, minimal, and sleek, not your usual cereal package design. Our design now is clunky and more along the lines of your generic cereal packaging (image attached). We are looking for something outside the box that will work with our cereal, the only coffee infused cereal available.
Updates

I have posted our old design and packaging. We will be using the aluminum "bag" with a label or design printed on it. We have to use the photo of the coffee beans that you can see on the old design but beyond that we want completely revamped. We are looking for modern, minimalist, yet sophisticated. This may be placed in the "specialty foods" isle as opposed to the cereal isle.

Industry/Entity Type

It Company

Colors
acd037
9bcb3c
f78f20
faa54b

```html
<!DOCTYPE html>
<html lang="en">
<head>
<meta charset="utf-8">
<title>Maple Drift Flakes – Pouch Label</title>
<link rel="stylesheet" href="https://fonts.googleapis.com/css2?family=Passion+One:wght@700&family=Yellowtail&display=swap">
<style>
  :root {
    --backdrop: #ecebe8;
    --foil-light: #b9b9b9;
    --foil-mid: #a3a3a3;
    --foil-dark: #8e8e8e;
    --seal-line: #c4c4c4;
    --ink-dark: #2b2b2b;
    --ink-light: #ffffff;
    --bean-dark: #3a2417;
    --bean-mid: #6b4631;
    --bean-light: #8a6a55;
  }
  html, body {
    margin: 0;
    padding: 0;
    width: 1200px;
    height: 960px;
    overflow: hidden;
    background: var(--backdrop);
  }
  .canvas {
    position: relative;
    width: 1200px;
    height: 960px;
  }
  .pouch {
    position: absolute;
    left: 325px;
    top: 130px;
    width: 552px;
    height: 700px;
  }
  .pouch-shape {
    position: absolute;
    inset: 0;
  }
  .hero-beans {
    position: absolute;
    right: 0;
    top: 14px;
    width: 230px;
    height: 260px;
    background: radial-gradient(ellipse at 60% 45%, var(--bean-mid) 0%, var(--bean-light) 35%, rgba(163,163,163,0) 72%);
    opacity: 0.85;
  }
  .bean-pile {
    position: absolute;
    left: 75px;
    top: 458px;
    width: 400px;
    height: 122px;
    border-radius: 0 0 200px 200px / 0 0 122px 122px;
    background: radial-gradient(ellipse at 50% 40%, var(--bean-mid) 0%, var(--bean-dark) 80%);
  }
  .product-name {
    position: absolute;
    left: 60px;
    top: 100px;
    margin: 0;
    font-family: "Passion One", "Arial Black", sans-serif;
    font-weight: 700;
    font-size: 92px;
    line-height: 84px;
    letter-spacing: 2px;
    color: var(--ink-dark);
    text-transform: uppercase;
  }
  .tagline {
    position: absolute;
    left: 60px;
    top: 312px;
    margin: 0;
    font-family: "Yellowtail", cursive;
    font-size: 30px;
    color: var(--ink-light);
  }
  .net-weight {
    position: absolute;
    left: 434px;
    top: 580px;
    margin: 0;
    font-family: "Yellowtail", cursive;
    font-size: 30px;
    color: var(--ink-light);
  }
</style>
</head>
<body>
<main class="canvas">
  <section class="pouch" aria-label="Maple Drift Flakes pouch label">
    <svg class="pouch-shape" width="552" height="700" viewBox="0 0 552 700" aria-hidden="true">
      <defs>
        <linearGradient id="foil" x1="0" y1="0" x2="1" y2="0">
          <stop offset="0" stop-color="var(--foil-mid)"/>
          <stop offset="0.15" stop-color="var(--foil-light)"/>
          <stop offset="0.5" stop-color="var(--foil-mid)"/>
          <stop offset="0.88" stop-color="var(--foil-light)"/>
          <stop offset="1" stop-color="var(--foil-dark)"/>
        </linearGradient>
        <pattern id="zigzag-top" width="12" height="8" patternUnits="userSpaceOnUse">
          <polygon points="0,8 6,0 12,8" fill="var(--foil-light)"/>
        </pattern>
        <pattern id="zigzag-bottom" width="12" height="8" patternUnits="userSpaceOnUse">
          <polygon points="0,0 6,8 12,0" fill="var(--foil-light)"/>
        </pattern>
      </defs>
      <rect x="0" y="0" width="552" height="8" fill="url(#zigzag-top)"/>
      <rect x="0" y="8" width="552" height="684" fill="url(#foil)"/>
      <rect x="0" y="692" width="552" height="8" fill="url(#zigzag-bottom)"/>
      <g class="seal-lines" stroke="var(--seal-line)" stroke-width="2">
        <line x1="0" y1="20" x2="552" y2="20"/>
        <line x1="0" y1="28" x2="552" y2="28"/>
        <line x1="0" y1="36" x2="552" y2="36"/>
        <line x1="0" y1="44" x2="552" y2="44"/>
        <line x1="0" y1="648" x2="552" y2="648"/>
        <line x1="0" y1="656" x2="552" y2="656"/>
        <line x1="0" y1="664" x2="552" y2="664"/>
        <line x1="0" y1="672" x2="552" y2="672"/>
      </g>
      <line class="tear-line" x1="0" y1="62" x2="552" y2="62" stroke="#6e6e6e" stroke-width="1.5" stroke-dasharray="8 5"/>
      <g class="arrow-row" fill="#ffffff">
        <rect x="0" y="74" width="18" height="6"/>
        <polygon points="18,70 28,77 18,84"/>
        <polygon points="40,71 49,77 40,83"/>
        <polygon points="58,71 67,77 58,83"/>
        <polygon points="76,71 85,77 76,83"/>
        <polygon points="94,71 103,77 94,83"/>
        <polygon points="112,71 121,77 112,83"/>
        <polygon points="130,71 139,77 130,83"/>
        <polygon points="148,71 157,77 148,83"/>
        <polygon points="166,71 175,77 166,83"/>
        <polygon points="184,71 193,77 184,83"/>
        <polygon points="202,71 211,77 202,83"/>
        <polygon points="220,71 229,77 220,83"/>
        <polygon points="238,71 247,77 238,83"/>
        <polygon points="256,71 265,77 256,83"/>
        <polygon points="274,71 283,77 274,83"/>
        <polygon points="292,71 301,77 292,83"/>
        <polygon points="310,71 319,77 310,83"/>
        <polygon points="328,71 337,77 328,83"/>
        <polygon points="346,71 355,77 346,83"/>
        <polygon points="364,71 373,77 364,83"/>
        <polygon points="382,71 391,77 382,83"/>
        <polygon points="400,71 409,77 400,83"/>
        <polygon points="418,71 427,77 418,83"/>
        <polygon points="436,71 445,77 436,83"/>
        <polygon points="454,71 463,77 454,83"/>
        <polygon points="472,71 481,77 472,83"/>
        <polygon points="490,71 499,77 490,83"/>
        <polygon points="508,71 517,77 508,83"/>
        <polygon points="526,71 535,77 526,83"/>
      </g>
    </svg>
    <div class="hero-beans" role="img" aria-label="Photo of roasted coffee beans, softly blurred"></div>
    <h1 class="product-name">Maple<br>Drift.</h1>
    <p class="tagline">Lightly Sweetened Coffee Cereal</p>
    <div class="bean-pile" role="img" aria-label="Photo of a pile of roasted coffee beans in a bowl-shaped window"></div>
    <p class="net-weight">65g</p>
  </section>
</main>
</body>
</html>
```